Lawn care business card

I am looking for a quality designed personal business card to represent the quality and elegant nature of our company. We separate ourselves in our market by the aesthetic value of our work, so I am looking for marketing material that does the same. We target our marketing high end customers, and we try to avoid price shoppers. I am open to all design options, so long as they are in line with our companies values.

We are tend to go with a retro look on everything from our logo and print material, to our uniforms. We like to portray and "old fashion" set of core values, with a modern elegance. So a wild and crazy look is out of the question.

Things I'd like on the card:
1.) Logo
2.) Phone number: (816) 555-2931
3.) Website: Verdelynkc.com
4.) Email: robertfairley@verdelynkc.com
5.) My name: Robert Fairley
6.) Facebook link: facebook.com/VerdelynGardenandGrounds
7.) Instagram: http://instagram.com/verdelynkc

Attached is a copy of our logo.

Reason: More time is needed to gather conclusive feedback from the members of our marketing team.

```html
<!DOCTYPE html>
<html lang="en">
<head>
<meta charset="utf-8">
<title>Verdelyn Garden &amp; Grounds – Business Card</title>
<link rel="stylesheet" href="https://fonts.googleapis.com/css2?family=Noto+Serif:ital,wght@1,700&family=Arimo:wght@400;700&display=swap">
<style>
  :root {
    --page: #ececec;
    --card-white: #ffffff;
    --band: #231f20;
    --ink: #1c1c1c;
    --accent: #ec5a24;
    --band-text: #ffffff;
  }
  * { box-sizing: border-box; margin: 0; padding: 0; }
  html, body { width: 1200px; height: 864px; overflow: hidden; }
  body {
    background: var(--page);
    font-family: "Arimo", Arial, sans-serif;
    position: relative;
  }
  .business-card {
    position: absolute;
    left: 100px; top: 146px;
    width: 1000px; height: 571px;
    background: var(--card-white);
    box-shadow: 0 10px 30px rgba(0,0,0,0.18);
    overflow: hidden;
  }
  .company-name {
    position: absolute;
    left: 80px; top: 118px;
    font-family: "Noto Serif", Georgia, serif;
    font-style: italic; font-weight: 700;
    font-size: 40px; letter-spacing: 1.5px;
    white-space: nowrap;
    color: var(--ink);
  }
  .person-name {
    position: absolute;
    left: 92px; top: 268px;
    font-size: 33px; letter-spacing: 1px;
    color: var(--ink);
  }
  .contact-band {
    position: absolute;
    left: 0; right: 0; top: 330px; bottom: 0;
    background: var(--band);
  }
  .contact-list {
    position: absolute;
    left: 92px; top: 30px;
    list-style: none;
  }
  .contact-item {
    display: flex; align-items: center;
    height: 38px;
    font-size: 22px; letter-spacing: 0.6px;
    white-space: nowrap;
    color: var(--band-text);
  }
  .contact-icon {
    width: 20px; height: 20px;
    margin-right: 18px; flex: none;
  }
  .brand-mark {
    position: absolute;
    right: 70px; top: 40px;
    display: flex; align-items: center;
  }
  .brand-dot {
    width: 76px; height: 76px; border-radius: 50%;
    background: var(--accent);
    margin-right: 18px;
  }
  .brand-name {
    font-size: 40px; font-weight: 700; letter-spacing: 2px;
    color: var(--band-text);
  }
</style>
</head>
<body>
  <article class="business-card">
    <h1 class="company-name">Verdelyn Garden &amp; Grounds LLC</h1>
    <p class="person-name">Robert Fairley</p>

    <section class="contact-band">
      <ul class="contact-list">
        <li class="contact-item">
          <svg class="contact-icon" viewBox="0 0 20 20" aria-hidden="true"><path fill="#ec5a24" d="M4 1.5l3.2 3.6-1.6 2.4c1.2 2.6 3.3 4.7 5.9 5.9l2.4-1.6 3.6 3.2-2 3C8.2 17.5 2.5 11.8 1 4z"/></svg>
          (816) 555-2931
        </li>
        <li class="contact-item">
          <svg class="contact-icon" viewBox="0 0 20 20" aria-hidden="true"><circle cx="10" cy="10" r="8.5" fill="none" stroke="#ec5a24" stroke-width="2"/><ellipse cx="10" cy="10" rx="3.5" ry="8.5" fill="none" stroke="#ec5a24" stroke-width="1.6"/><path d="M1.5 10h17" stroke="#ec5a24" stroke-width="1.6"/></svg>
          Verdelynkc.com
        </li>
        <li class="contact-item">
          <svg class="contact-icon" viewBox="0 0 20 20" aria-hidden="true"><rect x="1" y="4" width="18" height="12" fill="#ec5a24"/><path d="M1 4l9 7 9-7" fill="none" stroke="#231f20" stroke-width="1.6"/></svg>
          robertfairley@verdelynkc.com
        </li>
        <li class="contact-item">
          <svg class="contact-icon" viewBox="0 0 20 20" aria-hidden="true"><rect x="1" y="1" width="18" height="18" rx="3" fill="#ec5a24"/></svg>
          http://photolane.com/verdelynkc
        </li>
        <li class="contact-item">
          <svg class="contact-icon" viewBox="0 0 20 20" aria-hidden="true"><rect x="1" y="1" width="18" height="18" rx="3" fill="#ec5a24"/></svg>
          friendwall.com/VerdelynGardenandGrounds
        </li>
      </ul>

      <div class="brand-mark">
        <span class="brand-dot"></span>
        <span class="brand-name">VERDELYN</span>
      </div>
    </section>
  </article>
</body>
</html>
```